Law Offices business card

Hi there, I'll need business card for the Law Offices of Colin Matheny. The information must convey his strategic approach and quick resolution to complex business litigation needs. Please emphasize Civil Litigation, Corporate Law, Business Governance and Real Estate Law. Colin has over 25 years of experience in these fields.The card should be modern and edgy and the message should be clear. Please consult his current website for ideas.

```html
<!DOCTYPE html>
<html lang="en">
<head>
<meta charset="utf-8">
<title>Law Offices of Colin Matheny – Business Card</title>
<link rel="stylesheet" href="https://fonts.googleapis.com/css2?family=Arimo:wght@400;700&display=swap">
<style>
  :root {
    --page: #3a3a3c;
    --card: #0b0b0c;
    --card-edge: #1a1a1c;
    --ink: #f2f2f2;
    --accent: #b8383c;
    --accent-soft: rgba(184, 56, 60, 0.55);
  }
  * { margin: 0; padding: 0; box-sizing: border-box; }
  html, body {
    width: 1200px; height: 950px; overflow: hidden;
    background: var(--page);
    font-family: "Arimo", Arial, sans-serif;
  }
  .sheet {
    width: 1200px; height: 950px;
    display: flex; flex-direction: column;
    align-items: center; justify-content: center; gap: 40px;
  }
  .card {
    width: 735px; height: 420px;
    background: var(--card);
    border: 1px solid var(--card-edge);
    position: relative;
    display: flex; align-items: center; justify-content: center;
  }
  /* front */
  .firm {
    display: flex; align-items: center; gap: 18px;
  }
  .firm-square {
    width: 34px; height: 34px; background: var(--accent);
  }
  .firm-name {
    color: var(--ink);
    font-weight: 700;
    font-size: 34px;
    letter-spacing: 0.5px;
  }
  /* back */
  .contact {
    display: flex; flex-direction: column; align-items: center;
    color: var(--ink); text-align: center;
  }
  .contact-mark {
    width: 16px; height: 16px; background: var(--accent);
    margin-bottom: 26px;
  }
  .contact-person {
    font-size: 22px; color: var(--accent);
    padding: 0 40px 8px;
  }
  .contact-person .role { color: var(--ink); font-size: 18px; }
  .contact-rule {
    width: 520px; height: 1px;
    background: linear-gradient(90deg, transparent, var(--accent-soft) 15%, var(--accent) 50%, var(--accent-soft) 85%, transparent);
    margin-bottom: 14px;
  }
  .contact-line { font-size: 16px; line-height: 28px; }
  .label { color: var(--accent); }
  .contact-rule.bottom { margin: 12px 0 0; width: 420px; }
</style>
</head>
<body>
<main class="sheet">
  <section class="card card-front">
    <div class="firm">
      <span class="firm-square"></span>
      <span class="firm-name">Law Offices of Colin Matheny, PA</span>
    </div>
  </section>

  <section class="card card-back">
    <div class="contact">
      <span class="contact-mark"></span>
      <p class="contact-person">Evan Lark &nbsp;-&nbsp; <span class="role">President</span></p>
      <div class="contact-rule"></div>
      <p class="contact-line">4127 Harborview Lane, Glen Oaks, NY 11004</p>
      <p class="contact-line"><span class="label">P :</span> 555 0142 7781 <span class="label">M :</span> 555 0193 4462 <span class="label">F :</span> 555 0167 2209</p>
      <p class="contact-line"><span class="label">E :</span> evan@mathenylaw.com <span class="label">W :</span> www.mathenylaw.com</p>
      <div class="contact-rule bottom"></div>
    </div>
  </section>
</main>
</body>
</html>
```